BOLD & MINIMALIST DESIGN NEEDED

We want a very bold but minimalistic business card design that is impactful and utilizes both sides of the business card. Our current logo is included for your use.

We want bold fonts and good use of negative space. We don't want the logo to overpower the design.

Target Market(s)

Professionals who are building new commercial buildings.

Industry/Entity Type

Construction

Contact Information for Business Card

Name, Title, email, office phone, cell phone, website

Font styles to use
Serif
Sans Serif

Requirements
Must have
• Bold design!

```html
<!DOCTYPE html>
<html lang="en">
<head>
<meta charset="utf-8">
<title>Ridgeline Design + Build – Business Card</title>
<link rel="stylesheet" href="https://fonts.googleapis.com/css2?family=Montserrat:wght@700;800&family=Didact+Gothic&display=swap">
<style>
  :root {
    --page: #e9e7e3;
    --ink: #0b0c0d;
    --ink-soft: #1e2022;
    --paper: #ffffff;
    --paper-shade: #eceeed;
    --green: #6cc23a;
    --grey-text: #8a8d8f;
    --white: #ffffff;
  }
  * { box-sizing: border-box; margin: 0; padding: 0; }
  html, body { width: 1200px; height: 900px; overflow: hidden; }
  body {
    background: var(--page);
    display: flex;
    flex-direction: column;
    align-items: center;
    justify-content: center;
    gap: 56px;
    font-family: "Didact Gothic", "Century Gothic", sans-serif;
  }
  .card {
    position: relative;
    width: 560px;
    height: 320px;
    overflow: hidden;
    box-shadow: 0 10px 28px rgba(0,0,0,0.22);
  }

  /* Back side */
  .card-back {
    background: radial-gradient(ellipse at 50% 40%, #2b2d2f 0%, var(--ink-soft) 35%, var(--ink) 75%);
    display: flex;
    flex-direction: column;
    align-items: center;
    justify-content: center;
  }
  .back-brand {
    display: flex;
    align-items: center;
    gap: 12px;
    font-family: "Montserrat", sans-serif;
    font-weight: 800;
    font-size: 30px;
    letter-spacing: 3px;
    color: var(--green);
  }
  .brand-square { width: 18px; height: 18px; background: var(--green); }
  .back-rule {
    width: 300px;
    height: 1px;
    margin: 22px 0 16px;
    background: linear-gradient(90deg, transparent, rgba(255,255,255,0.55), transparent);
  }
  .back-web {
    font-family: "Montserrat", sans-serif;
    font-weight: 700;
    font-size: 13px;
    letter-spacing: 9px;
    color: var(--green);
  }

  /* Front side */
  .card-front {
    background: linear-gradient(100deg, var(--paper-shade) 0%, var(--paper) 55%);
  }
  .front-band { position: absolute; inset: 0; }
  .front-brand {
    position: absolute;
    left: 120px;
    top: 64px;
    display: flex;
    align-items: center;
    gap: 10px;
    font-family: "Montserrat", sans-serif;
    font-weight: 800;
    font-size: 22px;
    letter-spacing: 1px;
    color: var(--ink);
  }
  .front-brand .brand-square { width: 14px; height: 14px; background: var(--ink); }
  .person {
    position: absolute;
    left: 150px;
    top: 114px;
    text-align: center;
    width: 230px;
  }
  .person-name {
    font-family: "Montserrat", sans-serif;
    font-weight: 800;
    font-size: 19px;
    color: var(--ink);
  }
  .person-title {
    font-size: 15px;
    color: var(--grey-text);
    margin-top: 2px;
  }
  .contact {
    position: absolute;
    left: 262px;
    top: 212px;
    color: var(--white);
    font-size: 13px;
    line-height: 1.55;
  }
  .contact-row { display: flex; align-items: center; gap: 6px; white-space: nowrap; }
  .contact-sep { color: var(--white); margin: 0 4px; }
  .icon { width: 12px; height: 12px; flex: none; }
  .contact-rule {
    height: 1px;
    width: 270px;
    background: var(--green);
    margin: 6px 0 5px;
  }
</style>
</head>
<body>

  <section class="card card-back" aria-label="Card back">
    <div class="back-brand"><span class="brand-square"></span>RIDGELINE</div>
    <div class="back-rule"></div>
    <div class="back-web">www.rdb-build.com</div>
  </section>

  <section class="card card-front" aria-label="Card front">
    <svg class="front-band" viewBox="0 0 560 320" preserveAspectRatio="none" aria-hidden="true">
      <path d="M110 320 C170 220 300 168 560 150 L560 320 Z" fill="var(--ink)"/>
    </svg>

    <div class="front-brand"><span class="brand-square"></span>Ridgeline Design + Build</div>

    <div class="person">
      <div class="person-name">Jonah Whitfield</div>
      <div class="person-title">Founder</div>
    </div>

    <div class="contact">
      <div class="contact-row">
        <svg class="icon" viewBox="0 0 12 12" aria-hidden="true"><rect x="3" y="0.5" width="6" height="11" rx="1" fill="none" stroke="var(--green)" stroke-width="1.2"/></svg>
        <span>3XX-2XX-9XXX</span>
        <span class="contact-sep">|</span>
        <svg class="icon" viewBox="0 0 12 12" aria-hidden="true"><path d="M2 1.5 L4.5 1.5 L5.3 4 L4 5 C4.6 6.4 5.6 7.4 7 8 L8 6.7 L10.5 7.5 L10.5 10 C6 10.5 1.5 6 2 1.5 Z" fill="var(--green)"/></svg>
        <span>555-014-2200</span>
      </div>
      <div class="contact-row">
        <svg class="icon" viewBox="0 0 12 12" aria-hidden="true"><rect x="0.8" y="2.5" width="10.4" height="7" fill="var(--green)"/><path d="M0.8 2.5 L6 6.5 L11.2 2.5" fill="none" stroke="var(--ink)" stroke-width="1"/></svg>
        <span>info@rdb-build.com</span>
        <span class="contact-sep">|</span>
        <svg class="icon" viewBox="0 0 12 12" aria-hidden="true"><g fill="none" stroke="var(--green)" stroke-width="1"><circle cx="6" cy="6" r="5"/><ellipse cx="6" cy="6" rx="2.2" ry="5"/><path d="M1 6 H11 M2 3.5 H10 M2 8.5 H10"/></g></svg>
        <span>www.rdb-build.com</span>
      </div>
      <div class="contact-rule"></div>
      <div class="contact-row"><span>1420 Cedar Hollow Rd. Pine Ridge, GA 30000</span></div>
    </div>
  </section>

</body>
</html>
```